Book Cover Design Project for Thriller

I need a book cover for my thriller, 'Marra's Hollow.'

I will use this image primarily for e-publishing on e-readers, and hopefully someday on the front of a hardcover. It is very important that the image can be easily recognizable when it is in thumbnail view, just as one would see it while shopping online.

I would like my name, Peter L. Dunford to be on the top of the image, and the title, Marra's Hollow, to be on the bottom. The title needs to be larger than my name so that it stands out more.

Requirements (taken from Pagelit):
- Image dimensions of at least 500 by 800 pixels.
- A maximum of 2000 pixels on the longest side is preferred
- Ideal height/width ratio of 1.6

Images/items from the book that could be incorporated into the cover design are listed below in no particular order(please note: not all of these need to be included):
- Mountains & Forest (Story takes place in eastern Montana)
- Marine Corps emblem (Main character is a Marine)
- Red float plane flying over Montana, w/ engine on fire, going down.
- Silver Star military award
- Young man and young woman (both early 20s) holding hands while running through the woods and or mountains.
- A rifle (simple hunting type, no scope)
- A mountain stream

Here is a 'flap cover' summary of the book:
"Cal Brovant returns home to Montana from a tour as a Marine in Afghanistan wanting to escape into the wilderness. Marra Quistbeck is up and coming pop singer from Baltimore whose concert tour has sent her life into a downward spiral. When Cal disrupts the attempted kidnapping of Marra, he’s forced back into his familiar role as a Marine. Cal and Marra must evade her determined kidnappers through miles of uninhabited forests and mountains of western Montana. Despite their completely different lives, the two must learn to trust each other as they confront more than just the men who threaten to destroy them."

Thank you for considering this project!- Peter
Updates

Project Deadline Extended
Reason: I'm extending the deadline as I haven't received many submissions which I believe is partially due to the holidays.

Industry/Entity Type

Shopping

```html
<!DOCTYPE html>
<html lang="en">
<head>
<meta charset="utf-8">
<title>Marra's Hollow — Peter L. Dunford</title>
<link rel="stylesheet" href="https://fonts.googleapis.com/css2?family=Abril+Fatface&family=Ultra&display=swap">
<style>
  :root {
    --ink: #000000;
    --frame: #6e2013;
    --ember-dark: #8a2e10;
    --ember: #c4571a;
    --flame: #e8861c;
    --sun: #fff3c4;
    --smoke-light: #6a6a6a;
    --smoke-dark: #141414;
  }
  html, body {
    margin: 0;
    padding: 0;
    width: 960px;
    height: 1200px;
    overflow: hidden;
    background: var(--ink);
  }
  .cover {
    display: block;
    width: 960px;
    height: 1200px;
  }
  .author-name {
    font-family: "Ultra", "Rockwell Extra Bold", serif;
  }
  .book-title {
    font-family: "Abril Fatface", "Bodoni MT Black", serif;
  }
</style>
</head>
<body>
<svg class="cover" viewBox="0 0 960 1200" xmlns="http://www.w3.org/2000/svg">
  <defs>
    <linearGradient id="sunset-fill" gradientUnits="userSpaceOnUse" x1="0" y1="80" x2="0" y2="1000">
      <stop offset="0" stop-color="var(--ember-dark)"/>
      <stop offset="0.3" stop-color="var(--ember)"/>
      <stop offset="0.6" stop-color="var(--flame)"/>
      <stop offset="0.85" stop-color="#f29a24"/>
      <stop offset="1" stop-color="#a8401a"/>
    </linearGradient>
    <radialGradient id="sun-glow" gradientUnits="userSpaceOnUse" cx="600" cy="870" r="200">
      <stop offset="0" stop-color="var(--sun)"/>
      <stop offset="0.4" stop-color="#ffcf4a"/>
      <stop offset="1" stop-color="#f08a1e" stop-opacity="0"/>
    </radialGradient>
    <linearGradient id="smoke-fill" x1="0" y1="0" x2="1" y2="0">
      <stop offset="0" stop-color="var(--smoke-light)"/>
      <stop offset="1" stop-color="var(--smoke-dark)"/>
    </linearGradient>
  </defs>

  <rect class="frame" x="29" y="33" width="902" height="1138" fill="none" stroke="var(--frame)" stroke-width="8"/>

  <g class="author-name" fill="url(#sunset-fill)">
    <text x="134" y="178" font-size="124" textLength="672" lengthAdjust="spacingAndGlyphs">PETER L.</text>
    <text x="115" y="389" font-size="236" textLength="711" lengthAdjust="spacingAndGlyphs">DUNFORD</text>
  </g>

  <g class="book-title">
    <text x="72" y="720" font-size="336" textLength="797" lengthAdjust="spacingAndGlyphs" fill="url(#sunset-fill)">MARRA’S</text>
    <text x="77" y="989" font-size="336" textLength="825" lengthAdjust="spacingAndGlyphs" fill="url(#sunset-fill)">HOLLOW</text>
    <text x="77" y="989" font-size="336" textLength="825" lengthAdjust="spacingAndGlyphs" fill="url(#sun-glow)">HOLLOW</text>
  </g>

  <rect class="plane-illustration" x="33" y="1000" width="894" height="163" fill="url(#smoke-fill)" opacity="0.55"
        role="img" aria-label="Red float plane with its engine on fire, trailing smoke as it goes down over the forest"/>
</svg>
</body>
</html>
```